holloway paving service

Needs to have phone number 0418259730 and email markholloway@brightmail.com.au.
ABN 62318470915
name mark holloway

For all your concreting solutions
Excavation
Exposed & colour concrete
House & shed slabs
Driveways
Landing & steps

Contact Information for Business Card

ph 0418259730
email markholloway@brightmail.com.au.
ABN 62318470915
name mark holloway

```html
<!DOCTYPE html>
<html lang="en">
<head>
<meta charset="utf-8">
<title>Holloway Paving Service – Business Card</title>
<link href="https://fonts.googleapis.com/css2?family=Roboto+Condensed:wght@400;700&family=Roboto:wght@400;500&display=swap" rel="stylesheet">
<style>
  :root {
    --orange: #f26a21;
    --orange-deep: #e45f1a;
    --grey: #6d6e70;
    --card-white: #f7f7f7;
    --page: #e9e6e1;
    --white: #ffffff;
  }
  * { box-sizing: border-box; margin: 0; padding: 0; }
  html, body {
    width: 1200px; height: 950px; overflow: hidden;
    background: var(--page);
    font-family: "Roboto Condensed", "Roboto", Arial, sans-serif;
  }
  .canvas { position: relative; width: 1200px; height: 950px; }

  .card {
    position: absolute; width: 630px; height: 360px;
    box-shadow: 0 6px 18px rgba(0,0,0,0.18);
  }

  /* Front */
  .card-front { left: 60px; top: 90px; background: var(--card-white); }
  .contact-panel {
    position: absolute; left: 330px; top: 44px; width: 260px; height: 196px;
    background: var(--orange); border: 2px solid var(--grey);
    color: var(--white); padding: 26px 24px;
  }
  .contact-name {
    font-weight: 700; font-size: 25px; letter-spacing: 0.5px;
    text-transform: uppercase; margin-bottom: 12px;
  }
  .contact-list { list-style: none; font-size: 15px; line-height: 24px; }
  .contact-list li { display: flex; align-items: center; gap: 8px; }
  .contact-list svg { width: 12px; height: 12px; flex: none; }
  .contact-abn { margin-top: 4px; }

  .brand-lockup {
    position: absolute; left: 42px; top: 244px;
    display: flex; align-items: center; gap: 14px;
  }
  .brand-square { width: 54px; height: 54px; background: var(--orange); }
  .brand-rule { width: 2px; height: 74px; background: var(--orange); }
  .brand-text { line-height: 1.1; }
  .brand-name {
    color: var(--orange); font-weight: 700; font-size: 19px;
    text-transform: uppercase; letter-spacing: 0.3px;
  }
  .brand-sub {
    display: flex; align-items: center; gap: 6px;
    color: var(--grey); font-size: 13px; letter-spacing: 2px; text-transform: uppercase;
  }
  .brand-sub::before, .brand-sub::after {
    content: ""; width: 40px; height: 1px; background: var(--grey);
  }
  .brand-phone { color: var(--orange); font-size: 16px; letter-spacing: 0.5px; }

  /* Back */
  .card-back { left: 510px; top: 500px; background: var(--orange); color: var(--white); }
  .back-brand {
    position: absolute; left: 210px; top: 40px;
    display: flex; align-items: center; gap: 14px;
  }
  .back-square { width: 46px; height: 46px; background: var(--white); }
  .back-name {
    font-weight: 700; font-size: 26px; text-transform: uppercase; letter-spacing: 0.5px;
    line-height: 1.1;
  }
  .services {
    position: absolute; left: 28px; bottom: 28px;
    font-family: "Roboto", Arial, sans-serif; font-size: 16px; line-height: 24px;
  }
  .services .dot { font-size: 10px; vertical-align: 2px; margin: 0 6px; }
</style>
</head>
<body>
<main class="canvas">

  <section class="card card-front" aria-label="Business card front">
    <div class="contact-panel">
      <h1 class="contact-name">Mark Holloway</h1>
      <ul class="contact-list">
        <li>
          <svg viewBox="0 0 12 12" aria-hidden="true"><path d="M2.5 1l2 2.2-1 1.3a7 7 0 0 0 4 4l1.3-1 2.2 2-1.2 1.5C5.6 11 1 6.4 1 2.2z" fill="#fff"/></svg>
          0418259730
        </li>
        <li>
          <svg viewBox="0 0 12 12" aria-hidden="true"><rect x="1" y="2.5" width="10" height="7" fill="#fff"/><path d="M1 2.5l5 4 5-4" stroke="#f26a21" fill="none"/></svg>
          markholloway@brightmail.com.au
        </li>
        <li>
          <svg viewBox="0 0 12 12" aria-hidden="true"><circle cx="6" cy="6" r="5" fill="#fff"/><path d="M1 6h10M6 1c2 2 2 8 0 10M6 1c-2 2-2 8 0 10" stroke="#f26a21" fill="none" stroke-width="0.8"/></svg>
          www.hollowaypaving.com.au
        </li>
        <li class="contact-abn">ABN 62318470915</li>
      </ul>
    </div>

    <div class="brand-lockup">
      <div class="brand-square" aria-hidden="true"></div>
      <div class="brand-rule" aria-hidden="true"></div>
      <div class="brand-text">
        <div class="brand-name">Holloway Paving</div>
        <div class="brand-sub">Service</div>
        <div class="brand-phone">0418259730</div>
      </div>
    </div>
  </section>

  <section class="card card-back" aria-label="Business card back">
    <div class="back-brand">
      <div class="back-square" aria-hidden="true"></div>
      <div class="back-name">Holloway<br>Paving Service</div>
    </div>
    <p class="services">
      Excavation<span class="dot">◆</span>Exposed &amp; colour concrete<span class="dot">◆</span>House<br>
      &amp; shed slabs<span class="dot">◆</span>Driveways<span class="dot">◆</span>Landing &amp; steps
    </p>
  </section>

</main>
</body>
</html>
```